Slogan für Reisebüro
Zielgruppe
Wir sind ein Reisebüro in Fürth mit über 20 Jahren Erfahrung und sind Spezialisten für Fernreisen und Hochzeitsreisen. Mit unserem Imagewechsel wollen wir dem Kunden eine Art Concierge-Service anbieten.
Feinster Service endet für unsere Kunden selbstverständlich nicht nach Planung und Buchung der Reise. Unser Team sorgt im Vorfeld, sowie rund um die Uhr während der Reise, für vollste Zufriedenheit. Ob Sie spontan einen Tisch im besten Restaurant der Stadt benötigen, einen ganz besonderen Ausflug buchen möchten oder Anpassungen an der Reise vornehmen möchten. Wir sind jederzeit ansprechbar und helfen bei allen Fragen und Wünschen.
Die Philosophie ist eine unbeschwerte Art des Reisens. Dies fängt bei uns bereits während der Reiseplanung an und hört erst dann auf, wenn der Kunde es wünscht.
Wir stehen für:
Inhabergeführte, unabhängiges Unternehmen
Persönliche Ansprechpartner mit langjähriger Reiseexpertise
Der Blick über den Tellerrand für außergewöhnliche, maßgeschneiderte Reisekonzepte
24/7-Erreichbarkeit, Notfallservice und Soforthilfe vor, während und nach der Reise
Persönliche Beratung: objektiv, professionell und diskret
Insider-Tipps und Empfehlungen
Vor-Ort-Wunscherfüllung und persönlicher Reise-Concierge-Service: Tischreservierungen, Konzertkarten, spontane Eventplanung, VIP-Arrangement
Flexible, individuelle Beratungstermine, unabhängig von klassischen Öffnungszeiten, jederzeit nach vorheriger Terminvereinbarung
Um das zu unterstützen, haben wir letztes Jahr einen Namenswechsel von Wanderkiste auf Sonnweg Tours vorgenommen und suchen nun einen neuen Claim.
Aufgabenstellung
Wir suchen einen Claim, der zu unserem Service passt. Im Anhang findet Ihr außerdem unsere Unternehmensstrategie - (bitte beachtet nicht das Logo bzw. den Firmennamen; das ist noch unser alter Name).

```html
<!DOCTYPE html>
<html lang="de">
<head>
<meta charset="utf-8">
<title>Claim – Sonnweg Tours</title>
<link rel="stylesheet" href="https://fonts.googleapis.com/css2?family=Arimo:wght@400&display=swap">
<style>
  :root {
    --paper: #ffffff;
    --claim-blue: #0f93c3;
  }
  html, body {
    margin: 0;
    padding: 0;
    width: 1200px;
    height: 1200px;
    overflow: hidden;
    background: var(--paper);
  }
  .claim-canvas {
    width: 1200px;
    height: 1200px;
    display: flex;
    align-items: center;
    justify-content: center;
  }
  .claim-text {
    margin: 0;
    font-family: "Arimo", Arial, sans-serif;
    font-weight: 400;
    font-size: 56px;
    color: var(--claim-blue);
    letter-spacing: 0;
    white-space: nowrap;
    transform: translateY(-18px);
  }
</style>
</head>
<body>
  <main class="claim-canvas">
    <p class="claim-text">Damit Ihr Traumurlaub wahr wird!</p>
  </main>
</body>
</html>
```